Tolbek cards

I want a simple business card that pops.
Logo on one side.
On side two i want.
"Are you thinking about a new building on your property, or renovating an existing structure? Contact".....
Owners Name: Dale Whitacre
Owners Phone number: 610-555-0187
Address:4076 Copper Ridge RD, Alder Falls, PA 16874
Committed to Quality, Service, and Integrity

```html
<!DOCTYPE html>
<html lang="en">
<head>
<meta charset="UTF-8">
<title>Tolbek Builders LLC – Business Card</title>
<link rel="stylesheet" href="https://fonts.googleapis.com/css2?family=Poppins:wght@300;400;600&display=swap">
<style>
  :root {
    --page-bg: #d8cec2;
    --front-top: #86755f;
    --front-bottom: #3e2a1a;
    --card-back: #ffffff;
    --ink: #3a2616;
    --rule: #3a2616;
    --logo-ink: #ffffff;
  }
  * { margin: 0; padding: 0; box-sizing: border-box; }
  html, body {
    width: 1189px;
    height: 1200px;
    overflow: hidden;
  }
  body {
    position: relative;
    background: var(--page-bg);
    font-family: "Poppins", sans-serif;
    color: var(--ink);
  }
  .card {
    position: absolute;
    left: 169px;
    width: 851px;
    height: 485px;
    border-radius: 34px;
    box-shadow: 0 8px 22px rgba(40, 25, 12, 0.28);
  }
  .card--front {
    top: 112px;
    background: linear-gradient(180deg, var(--front-top) 0%, #5f4b37 35%, var(--front-bottom) 100%);
    display: flex;
    align-items: center;
    justify-content: center;
  }
  .brand-name {
    color: var(--logo-ink);
    font-weight: 600;
    font-size: 46px;
    letter-spacing: 1px;
    text-transform: uppercase;
  }
  .card--back {
    top: 641px;
    background: var(--card-back);
  }
  .intro {
    position: absolute;
    top: 140px;
    left: 0;
    width: 100%;
    text-align: center;
    font-size: 21px;
    line-height: 27px;
    font-weight: 400;
  }
  .contact-row {
    position: absolute;
    top: 213px;
    left: 114px;
    width: 622px;
    height: 94px;
    border-top: 1.5px solid var(--rule);
    border-bottom: 1.5px solid var(--rule);
  }
  .contact-row__divider {
    position: absolute;
    left: 310px;
    top: 0;
    bottom: 0;
    border-left: 1.5px solid var(--rule);
  }
  .owner {
    position: absolute;
    right: 340px;
    top: 18px;
    text-align: right;
  }
  .owner__name {
    font-weight: 600;
    font-size: 24px;
    line-height: 30px;
    text-transform: uppercase;
  }
  .owner__phone {
    font-size: 20px;
    line-height: 26px;
    display: flex;
    align-items: center;
    justify-content: flex-end;
    gap: 6px;
  }
  .owner__phone svg { width: 20px; height: 20px; }
  .address {
    position: absolute;
    left: 340px;
    top: 17px;
    font-size: 20px;
    line-height: 28px;
  }
  .tagline {
    position: absolute;
    top: 324px;
    left: 0;
    width: 100%;
    text-align: center;
    font-size: 19px;
    font-weight: 300;
    letter-spacing: 2.2px;
    text-transform: uppercase;
  }
</style>
</head>
<body>
  <section class="card card--front">
    <div class="brand-name">Tolbek Builders LLC</div>
  </section>

  <section class="card card--back">
    <p class="intro">Are you thinking about a new building on your property,<br>or renovating an existing structure? Contact</p>
    <div class="contact-row">
      <div class="owner">
        <div class="owner__name">Dale Whitacre</div>
        <div class="owner__phone">
          <svg viewBox="0 0 20 20" aria-hidden="true">
            <circle cx="10" cy="10" r="10" fill="#5a4330"/>
            <path d="M7.2 4.8c.4-.2.8 0 1 .4l.9 2c.2.4 0 .8-.3 1l-.8.6c.5 1.3 1.4 2.3 2.6 3l.7-.7c.3-.3.7-.4 1.1-.2l1.9 1c.4.2.5.6.4 1l-.4 1.1c-.2.5-.7.8-1.2.7-3.6-.6-6.4-3.5-6.9-7.1-.1-.5.2-1 .6-1.2z" fill="#ffffff"/>
          </svg>
          <span>610-555-0187</span>
        </div>
      </div>
      <div class="contact-row__divider"></div>
      <div class="address">4076 Copper Ridge RD,<br>Alder Falls, PA 16874</div>
    </div>
    <p class="tagline">Committed to Quality | Service | and Integrity</p>
  </section>
</body>
</html>
```